New Innovative Counselling and psychotherapy Service needs Business Card design

Keep it simple and professional. On one side, just company name and logo (perhaps in all blue) and maybe a tag line.

On other side (all white) my name and Qualifications in centre

Industry/Entity Type

Health And Wellness

Contact Information for Business Card

Dara Whelby
Counsellor & Psychotherapist
BSc (Psychol.), BA, Dip. (Couns. & Psych.), PG.Cert (CBT), FGTrK, ONRE

I will also require Mobile no, Email and web site address of which I'll pass on to final designer.

Font styles to use
Sans Serif

Requirements
Must have
• My Logo Only and please use the colours in logo that is in it.
Should not have
• Any other images

```html
<!DOCTYPE html>
<html lang="en">
<head>
<meta charset="utf-8">
<title>Kindred Lane – Business Card</title>
<link rel="stylesheet" href="https://fonts.googleapis.com/css2?family=Roboto:wght@400;700&display=swap">
<style>
  :root {
    --backdrop: #e4e5e7;
    --sky: #50b6eb;
    --brand-blue: #4a9fd5;
    --leaf: #86c152;
    --ink: #3a3a3c;
    --paper: #ffffff;
    --icon-teal: #3aa39a;
  }
  * { margin: 0; padding: 0; box-sizing: border-box; }
  html, body { width: 1200px; height: 726px; overflow: hidden; }
  body {
    background: var(--backdrop);
    font-family: "Roboto", Arial, sans-serif;
    color: var(--ink);
    position: relative;
  }
  .card {
    position: absolute;
    top: 198px;
    width: 540px;
    height: 330px;
    box-shadow: 0 8px 22px rgba(0,0,0,0.12);
  }
  .card--front { left: 40px; background: var(--sky); }
  .card--back { left: 620px; background: var(--paper); }

  .front-brand {
    position: absolute;
    left: 0; right: 0; top: 50%;
    transform: translateY(-50%);
    display: flex;
    flex-direction: column;
    align-items: center;
    color: var(--paper);
  }
  .front-brand__row { display: flex; align-items: center; gap: 16px; }
  .brand-dot { width: 46px; height: 46px; border-radius: 50%; background: var(--paper); }
  .front-brand__name { font-size: 40px; font-weight: 400; letter-spacing: 0.5px; }
  .front-brand__tagline {
    margin-top: 8px;
    margin-left: 62px;
    font-size: 15px;
    letter-spacing: 6px;
  }

  .back-brand {
    position: absolute;
    left: 46px; top: 92px;
    width: 200px;
    display: flex;
    flex-direction: column;
    align-items: center;
  }
  .back-brand .brand-dot { width: 96px; height: 96px; background: var(--brand-blue); }
  .back-brand__name {
    margin-top: 18px;
    font-size: 26px;
    font-weight: 400;
    color: var(--ink);
  }

  .details {
    position: absolute;
    left: 268px; top: 68px;
    right: 20px;
  }
  .details__name { font-size: 24px; font-weight: 700; color: var(--brand-blue); }
  .details__role, .details__quals { font-size: 11.5px; line-height: 1.35; color: var(--ink); }
  .details__role { margin-top: 2px; }
  .contact { margin-top: 20px; list-style: none; }
  .contact__item {
    display: flex; align-items: center; gap: 12px;
    font-size: 14px; line-height: 1.55; color: var(--ink);
  }
  .contact__icon { width: 13px; height: 13px; flex: none; }
</style>
</head>
<body>
  <section class="card card--front" aria-label="Card front">
    <div class="front-brand">
      <div class="front-brand__row">
        <span class="brand-dot" aria-hidden="true"></span>
        <span class="front-brand__name">Kindred Lane</span>
      </div>
      <p class="front-brand__tagline">A tag line goes here</p>
    </div>
  </section>

  <section class="card card--back" aria-label="Card back">
    <div class="back-brand">
      <span class="brand-dot" aria-hidden="true"></span>
      <span class="back-brand__name">Kindred Lane</span>
    </div>

    <div class="details">
      <h1 class="details__name">Dara Whelby</h1>
      <p class="details__role">Counsellor &amp; Psychotherapist</p>
      <p class="details__quals">BSc (Psychol.), BA, Dip. (Couns. &amp; Psych.),<br>PG.Cert (CBT), FGTrK, ONRE</p>
      <ul class="contact">
        <li class="contact__item">
          <svg class="contact__icon" viewBox="0 0 16 16" aria-hidden="true"><path fill="var(--icon-teal)" d="M3 1h3l1.5 4-2 1.3a9 9 0 0 0 4.2 4.2L11 8.5l4 1.5v3a2 2 0 0 1-2 2A12 12 0 0 1 1 3a2 2 0 0 1 2-2z"/></svg>
          0161 482 7305
        </li>
        <li class="contact__item">
          <svg class="contact__icon" viewBox="0 0 16 16" aria-hidden="true"><rect x="1" y="3" width="14" height="10" rx="1" fill="var(--icon-teal)"/><path d="M1.5 3.5 8 9l6.5-5.5" fill="none" stroke="#fff" stroke-width="1.2"/></svg>
          dara.w@KindredLane.com
        </li>
        <li class="contact__item">
          <svg class="contact__icon" viewBox="0 0 16 16" aria-hidden="true"><circle cx="8" cy="8" r="6.5" fill="none" stroke="var(--icon-teal)" stroke-width="1.4"/><ellipse cx="8" cy="8" rx="2.8" ry="6.5" fill="none" stroke="var(--icon-teal)" stroke-width="1.2"/><path d="M1.5 8h13" stroke="var(--icon-teal)" stroke-width="1.2"/></svg>
          www.KindredLane.com
        </li>
      </ul>
    </div>
  </section>
</body>
</html>
```